Corporate brochure design 4 pages

Hi,

We are a real estate company based in Europe.

We have almost finalized a rebranding.

We are developing a brand book guidelines (still on working process) to help you undertstand the look and feel of our new CI. I would like to receive proposals of design for a corporate brochure template. I need to receive the Indesign files with full ownership rights to be able to adapt all our documentation with this template.
Regarding the images, you can take gabaris on www.pelvarimages.example. I will be able to take them afterwards.

There will be 4 pages. you will receive the 4 pages on pdf for your consideration with our (almost) actual layout.

- 1st page: cover
- 2nd page: company presentation in french and english
- 3rd page: some market data + graph
- 4th page: 2 retail centers presentation.

In the template, i need to have:
- the paragraph styles in order
- 2 different masters with top/bottom/page number aso.

Please feel free to ask any other questions.

best regards,
Updates

I would like to precise tha t we are active on the commercial real estate sector:

- office transactions (rent /sales)
- property management of administrative and business buildings
- Valuation of properties
- Capital markets (investment advices for selling building)

Industry/Entity Type

Real Estate

Colors

Designer to choose colors to be used in the design.

```html
<!DOCTYPE html>
<html lang="fr">
<head>
<meta charset="utf-8">
<title>Corvane – Office Market Report Q3-2013 – Brochure Template</title>
<link href="https://fonts.googleapis.com/css2?family=Questrial&family=Titillium+Web:wght@600;700&display=swap" rel="stylesheet">
<style>
  :root{
    --ink:#0d0d0d;
    --orange:#f05a1a;
    --white:#ffffff;
    --stage:#ececec;
    --map:#dfe3e8;
    --photo-sky:#4f6f94;
    --photo-dark:#1d2838;
    --body-font:"Questrial", "Century Gothic", sans-serif;
    --head-font:"Titillium Web", "Century Gothic", sans-serif;
  }
  *{box-sizing:border-box;margin:0;padding:0}
  html,body{width:908px;height:1200px;overflow:hidden;background:var(--stage)}
  body{position:relative;font-family:var(--body-font);color:var(--white)}
  h1,h2{font-weight:400}
  .page{position:absolute;width:372px;height:525px;overflow:hidden}
  .page--dark{background:var(--ink)}
  .page--light{background:var(--white);color:var(--ink)}
  .abs{position:absolute}

  /* cover */
  .cover{left:70px;top:56px}
  .cover__photo{left:0;top:0;width:372px;height:247px;
    background:linear-gradient(160deg,var(--photo-sky) 0%,#8aa6c4 35%,#2e4563 70%,var(--photo-dark) 100%)}
  .cover__title{left:59px;top:265px;font-size:15px;line-height:17px;letter-spacing:.2px;font-weight:400}
  .cover__title strong{display:block;font-family:var(--head-font);font-weight:700;color:var(--orange);font-size:16px}
  .brand{left:166px;top:444px}
  .brand__name{font-family:var(--head-font);font-weight:700;font-size:40px;line-height:40px;letter-spacing:-1px;color:var(--white)}
  .brand__tag{margin-top:2px;font-size:10px;letter-spacing:2.6px;color:var(--orange)}

  /* team */
  .team{left:465px;top:56px}
  .kicker{font-size:11px;letter-spacing:.2px}
  .kicker--orange{color:var(--orange)}
  .heading{font-family:var(--head-font);font-weight:700;font-size:17px;line-height:20px;margin-top:5px}
  .heading--orange{color:var(--orange)}
  .col{top:18px;width:162px}
  .col--fr{left:18px}
  .col--en{left:194px}
  .copy{margin-top:10px;font-size:6.5px;line-height:8.1px;text-align:justify;hyphens:auto}
  .copy--orange{color:var(--orange)}
  .team__caption{right:56px;top:262px;font-size:6px;font-weight:700;color:var(--orange);font-family:var(--head-font)}
  .team__photo{left:0;top:277px;width:372px;height:248px;
    background:linear-gradient(120deg,#c9ced4 0%,#8b96a3 40%,#2b3340 75%,#1a1f27 100%);
    clip-path:polygon(0 0,322px 0,372px 70px,372px 248px,30px 248px,0 205px)}
  .folio{font-size:7px}
  .team .folio{left:14px;top:508px;color:var(--white)}

  /* stock */
  .stock{left:70px;top:614px}
  .runhead{top:18px;font-size:5.5px;letter-spacing:.1px}
  .runhead--fr{left:18px;color:var(--orange)}
  .runhead--en{left:195px}
  .stock .heading{position:absolute;top:34px;font-size:17px}
  .stock .copy{position:absolute;top:62px;width:162px;margin:0;font-size:6.5px}
  .stock-table{left:18px;top:121px;width:336px;font-size:5.5px}
  .stock-table .row{display:grid;grid-template-columns:129px 92px 52px 63px;height:9.6px;align-items:center}
  .stock-table .row span:nth-child(3),.stock-table .row span:nth-child(4){text-align:right;padding-right:4px}
  .stock-table .row--band{background:var(--orange)}
  .stock-table .row--head{background:var(--orange);height:8px}
  .stock-table .region{padding-left:3px}
  .stock-table .grand{margin-top:20px}
  .stock-table .label-total{text-align:right;padding-right:6px}
  .chart{left:100px;top:386px;width:260px;height:120px}
  .corner{left:0;bottom:0;width:42px;height:50px;background:var(--orange);clip-path:polygon(0 0,100% 100%,0 100%)}
  .stock .folio{left:15px;top:508px}
  .footer-name{left:41px;top:507px;font-size:8.5px;letter-spacing:.2px}

  /* retail */
  .retail{left:463px;top:614px}
  .retail__title{left:18px;font-size:15px;line-height:17px;font-weight:400}
  .retail__title--orange{color:var(--orange)}
  .map{left:216px;width:130px;height:92px;background:radial-gradient(ellipse at 50% 50%,#c6ced8 0%,var(--map) 55%,#f3f4f6 100%)}
  .street{left:18px;width:88px;height:49px;background:linear-gradient(180deg,#8f9aa8 0%,#5b6675 55%,#3a3f47 100%)}
  .facts{left:18px;width:336px;display:grid;grid-template-columns:88px 248px;font-size:5px}
  .facts .k{background:var(--orange);color:var(--white);padding:1px 3px;border-bottom:1px solid #e04e10;line-height:5.6px}
  .facts .v{padding:1px 4px;font-size:6px;line-height:6.6px;color:var(--ink)}
  .facts .v--band{background:var(--orange);color:#ffb08c;font-size:4.5px}
  .retail .folio{left:17px;top:508px;color:var(--white)}
  .retail .footer-name{color:var(--orange)}
</style>
</head>
<body>

<!-- cover -->
<section class="page page--dark cover">
  <div class="abs cover__photo" role="img" aria-label="Upward view of glass office towers against a blue sky"></div>
  <h1 class="abs cover__title">LUXEMBOURG<strong>OFFICE MARKET REPORT</strong>Q3-2013</h1>
  <div class="abs brand">
    <div class="brand__name">CORVANE</div>
    <div class="brand__tag">COMMERCIAL REAL ESTATE</div>
  </div>
</section>

<!-- team -->
<section class="page page--dark team">
  <div class="abs col col--fr">
    <p class="kicker kicker--orange">A PROPOS DE NOUS</p>
    <h2 class="heading">UNE ÉQUIPE</h2>
    <p class="copy">Proposer des services de qualité répondant parfaitement à vos attentes est notre ambition. Elle est partagée par tous les membres de notre équipe.<br>Notre connaissance du marché luxembourgeois, nos compétences et notre engagement dans les missions qui nous sont confiées font de Meridian Estates l’acteur majeur de l’immobilier d’entreprise au Grand-Duché. Nous sommes fiers de cette position et nous travaillons tous les jours pour la conserver.<br>Viser l’excellence suppose de savoir améliorer sans cesse nos prestations pour répondre le plus précisément à vos besoins. Venez nous consulter, vous constaterez que nos collaborateurs prennent le temps de vous écouter pour bien comprendre votre demande. Leur professionnalisme, leur savoir-faire et leur mobilisation nous permettront de trouver la solution.</p>
  </div>
  <div class="abs col col--en" lang="en">
    <p class="kicker">ABOUT US</p>
    <h2 class="heading heading--orange">A TEAM</h2>
    <p class="copy copy--orange">Our ambition is to offer quality services that perfectly meet your expectations. This ambition is shared by all members of the team.<br>Thanks to our knowledge of the Luxembourg market, our skills and our commitment to the missions entrusted to us, Meridian Estates is the undisputed leader in commercial real estate in the Grand Duchy. We are proud of this position and work hard to deserve it every day.<br>Targeting excellence means the constant improvement of our services in order to more accurately meet your needs. When you meet with us, you will find that our employees take the necessary time to listen to you and to correctly understand your need. Their professionalism, know-how and mobilisation will ensure that we find the right solution.</p>
  </div>
  <p class="abs team__caption">Étienne Morvaux, Julien Castel, Marc Heldrin, Frank Osterwald</p>
  <div class="abs team__photo" role="img" aria-label="Group portrait of the four partners in dark suits in an office lobby"></div>
  <span class="abs folio">01</span>
</section>

<!-- stock -->
<section class="page page--dark stock">
  <p class="abs runhead runhead--fr">RAPPORT DE MARCHÉ BUREAUX LUXEMBOURG Q3-2013</p>
  <p class="abs runhead runhead--en">LUXEMBOURG OFFICE MARKET REPORT Q3-2013</p>
  <h2 class="heading" style="left:18px">STOCK</h2>
  <h2 class="heading heading--orange" style="left:195px">STOCK</h2>
  <p class="copy" style="left:18px">Le stock de mètres carrés disponibles de bureaux a augmenté de 0,36 % au troisième trimestre de cette année grâce à la livraison de près de 12 300 m². Le stock total équivaut à 3 465 600 m².</p>
  <p class="copy copy--orange" style="left:195px" lang="en">The stock of available office square meters has increased by 0.36% during the third quarter of this year with the delivery of 12,300 m². The total stock reaches 3,465,600 sm².</p>

  <div class="abs stock-table">
    <div class="row row--head"><span></span><span>QUARTIERS-DISTRICTS</span><span>STOCK M²</span><span>STOCK %</span></div>
    <div class="row"><span class="region">CENTRE-VILLE (CITY)</span><span>Kirchberg</span><span>915 000</span><span>26,42 %</span></div>
    <div class="row row--band"><span></span><span>CBD</span><span>806 400</span><span>23,27 %</span></div>
    <div class="row"><span></span><span>Station</span><span>382 700</span><span>11,04 %</span></div>
    <div class="row row--band"><span></span><span>Cloche d’Or</span><span>365 600</span><span>10,55 %</span></div>
    <div class="row"><span></span><span>Limpertsberg</span><span>85 000</span><span>2,45 %</span></div>
    <div class="row row--band"><span></span><span>Belair / Merl</span><span>67 800</span><span>1,96 %</span></div>
    <div class="row"><span></span><span>Hamm</span><span>44 500</span><span>1,28 %</span></div>
    <div class="row row--band"><span></span><span>Kalchesbrück</span><span>33 000</span><span>0,95 %</span></div>
    <div class="row"><span></span><span class="label-total">TOTAL</span><span>2 700 500</span><span>77,92 %</span></div>
    <div class="row row--band"><span class="region">VILLE-PÉRIPHÉRIE (CITY-PERIPHERY)</span><span>Airport - Findel</span><span>157 500</span><span>4,54 %</span></div>
    <div class="row"><span></span><span>Bertrange / Bourmicht</span><span>82 000</span><span>2,37 %</span></div>
    <div class="row row--band"><span></span><span>Strassen</span><span>81 050</span><span>2,34 %</span></div>
    <div class="row"><span></span><span>Howald</span><span>62 600</span><span>1,81 %</span></div>
    <div class="row row--band"><span></span><span class="label-total">TOTAL</span><span>383 150</span><span>11,06 %</span></div>
    <div class="row"><span class="region">PÉRIPHÉRIE (PERIPHERY)</span><span>Belval</span><span>93 090</span><span>2,69 %</span></div>
    <div class="row row--band"><span></span><span>Capellen</span><span>69 500</span><span>2,01 %</span></div>
    <div class="row"><span></span><span>Leudelange</span><span>73 556</span><span>2,12 %</span></div>
    <div class="row row--band"><span></span><span>Munsbach</span><span>60 100</span><span>1,73 %</span></div>
    <div class="row"><span></span><span>Windhof</span><span>40 600</span><span>1,17 %</span></div>
    <div class="row row--band"><span></span><span>Esch-sur-Alzette</span><span>24 700</span><span>0,71 %</span></div>
    <div class="row"><span></span><span>Contern</span><span>20 400</span><span>0,59 %</span></div>
    <div class="row row--band"><span></span><span class="label-total">TOTAL</span><span>381 946</span><span>11,02 %</span></div>
    <div class="row row--band grand"><span></span><span class="label-total">TOTAL</span><span>3 465 596</span><span></span></div>
  </div>

  <svg class="abs chart" viewBox="0 0 260 120" aria-label="Office stock 2003 to YTD-2013 in thousand m²">
    <g font-family="Questrial, sans-serif" font-size="3.6" fill="#fff">
      <circle cx="66" cy="6" r="4.5" fill="#f05a1a"/>
      <text x="246" y="5" text-anchor="end" font-size="3">Source: Meridian Research</text>
      <g text-anchor="end">
        <text x="56" y="14">3,500</text><text x="56" y="27">3,200</text><text x="56" y="40">2,900</text>
        <text x="56" y="53">2,600</text><text x="56" y="66">2,300</text><text x="56" y="79">2,000</text><text x="56" y="92">1,700</text>
      </g>
      <g stroke="#555" stroke-width=".3" stroke-dasharray="1 1">
        <line x1="70" y1="13" x2="70" y2="91"/><line x1="87" y1="13" x2="87" y2="91"/><line x1="103" y1="13" x2="103" y2="91"/>
        <line x1="120" y1="13" x2="120" y2="91"/><line x1="136" y1="13" x2="136" y2="91"/><line x1="153" y1="13" x2="153" y2="91"/>
        <line x1="170" y1="13" x2="170" y2="91"/><line x1="186" y1="13" x2="186" y2="91"/><line x1="203" y1="13" x2="203" y2="91"/>
        <line x1="219" y1="13" x2="219" y2="91"/><line x1="236" y1="13" x2="236" y2="91"/>
      </g>
      <line x1="60" y1="91" x2="248" y2="91" stroke="#fff" stroke-width=".4"/>
      <g fill="#fff">
        <rect x="64" y="67.6" width="12" height="23.4"/><rect x="81" y="59" width="12" height="32"/>
        <rect x="97" y="52.8" width="12" height="38.2"/><rect x="114" y="48" width="12" height="43"/>
        <rect x="130" y="43.8" width="12" height="47.2"/><rect x="147" y="38.5" width="12" height="52.5"/>
        <rect x="164" y="27" width="12" height="64"/><rect x="180" y="25" width="12" height="66"/>
        <rect x="197" y="20.6" width="12" height="70.4"/><rect x="213" y="15.6" width="12" height="75.4"/>
        <rect x="230" y="14.5" width="12" height="76.5"/>
      </g>
      <g fill="#f05a1a" text-anchor="middle" font-size="3.2">
        <text x="70" y="66">2,241</text><text x="87" y="57">2,440</text><text x="103" y="51">2,582</text>
        <text x="120" y="46">2,693</text><text x="136" y="42">2,790</text><text x="153" y="37">2,912</text>
        <text x="170" y="25">3,176</text><text x="186" y="23">3,223</text><text x="203" y="19">3,325</text>
        <text x="219" y="14">3,440</text><text x="236" y="13">3,465</text>
      </g>
      <g text-anchor="middle" font-size="3.2">
        <text x="70" y="97">2003</text><text x="87" y="97">2004</text><text x="103" y="97">2005</text>
        <text x="120" y="97">2006</text><text x="136" y="97">2007</text><text x="153" y="97">2008</text>
        <text x="170" y="97">2009</text><text x="186" y="97">2010</text><text x="203" y="97">2011</text>
        <text x="219" y="97">2012</text><text x="236" y="97">YTD-2013</text>
      </g>
      <rect x="218" y="106" width="26" height="5" fill="#fff"/>
      <text x="218" y="115" font-size="3">Stock</text>
    </g>
  </svg>

  <div class="abs corner"></div>
  <span class="abs folio">02</span>
  <span class="abs footer-name">MERIDIAN ESTATES</span>
</section>

<!-- retail -->
<section class="page page--light retail">
  <h2 class="abs retail__title" style="top:28px">HIGH STREETS<br>LUXEMBOURG:<br>CITY - PEDESTRIAN ZONE</h2>
  <div class="abs map" style="top:22px" role="img" aria-label="Map of Luxembourg city highlighting the pedestrian zone"></div>
  <div class="abs street" style="top:86px" role="img" aria-label="Shoppers on a pedestrian shopping street"></div>
  <div class="abs facts" style="top:144px">
    <div class="k">Zone - Zone</div><div class="v v--band">Ville haute, rues piétonnes du centre</div>
    <div class="k">Stock - Stock</div><div class="v">51 500 m² - sqm</div>
    <div class="k">Magasins - Shops</div><div class="v v--band"></div>
    <div class="k" style="height:13px">Niveau loyers - Rental bands<br><span style="font-size:3.5px">(euros/sqm-m²/année-year)+TVA-VAT</span></div><div class="v">960 – 1 320</div>
    <div class="k">Parking</div><div class="v v--band"></div>
    <div class="k" style="height:44px">Marques principales - Main brands</div><div class="v">Velmora, T&amp;R, Lusien Vardel, Castrelle, Brenvik, Cafforadi, Aurivelle, Sable &amp; Lumière, Kristavel (flagship store Benelux), Delcourvin, Harwenne, Pic-Noirval, Petivanne, Modellia, Vera Stilvo, Frezkado, Finn &amp; Fordal, Belsquine, Velisande, QRVV, Tweed &amp; Tonic, Marlow Kentrey, Quillane, Cordevelle, Quayline Store, Vue Clairval, Aubrevin, Fenmorrow, Renzo Vallioni, ...</div>
  </div>

  <h2 class="abs retail__title retail__title--orange" style="top:272px">HIGH STREETS<br>LUXEMBOURG STATION<br>AV. GARE</h2>
  <div class="abs map" style="top:255px" role="img" aria-label="Map of Luxembourg city highlighting the station district"></div>
  <div class="abs street" style="top:333px" role="img" aria-label="Shopping avenue near the railway station"></div>
  <div class="abs facts" style="top:390px">
    <div class="k">Zone - Zone</div><div class="v v--band">Quartier Gare, avenue principale</div>
    <div class="k">Stock - Stock</div><div class="v">37 500 m² - sqm</div>
    <div class="k">Magasins - Shops</div><div class="v v--band"></div>
    <div class="k" style="height:13px">Niveau loyers - Rental bands<br><span style="font-size:3.5px">(euros/sqm-m²/année-year)+TVA-VAT</span></div><div class="v">300 – 720 euros/sqm/year</div>
    <div class="k">Parking</div><div class="v v--band"></div>
    <div class="k" style="height:37px">Marques principales - Main brands</div><div class="v">T&amp;R, Voltrenix, Tarnello, Urban Deckard, Casa Lumenta, Pastellon, Janelvie, M&amp;V, DUBRA, ZQ, Fildorine, Belsquine, Pas Légeron, Ilsavée, Optivrenne, Burgo Bayne, Pralinorée, Velindra, Herbalienne, Rive Huitième, Allée Verdine, Fenmorrow, Solennix, Marchévo, Inês Rochal, Taillvern</div>
  </div>

  <div class="abs corner"></div>
  <span class="abs folio">03</span>
  <span class="abs footer-name">RETAIL CENTRE</span>
</section>

</body>
</html>
```